I need a flyer made , the flyer can be one page or two pages or three pages . I will be posting this on Instagram and social media platforms. I am a luxury home builder , I am looking to hire a construction project manager . Below are some examples and ideas what can be on the flyer

We’re looking for a construction project manager who’s passionate about building luxury homes at the highest standards
We’re hiring construction project manager
* Experience 5+ years in residential project management with a strong portfolio of completed homes.
* location : Bergen County NJ
* excellent leadership skills, leads teams with confidence and clarity
* communicates seamlessly with architects , engineers, designers and clients
*knows how to manage budgets and timelines without compromising quality
*solves problems with a positive solution first mindset
* pays attention to every detail because in luxury the small things are the big things

Apply now , link in bio or DM to connect.

My logo is attached, my web site www.velstridebuilders.com
My style is modern but still warm and inviting. I like a clean classy look .

Please don’t add any images of chairs or people to the flyer , I do not want people on my flyer. Do not add standard images of offices and houses , we are luxury builders , we build homes over 2 million dollars. Keep a classy , simple modern look . High end .

You can add a white hard hat with my logo on it for a image , this is a suggestion does not have to be on my flyer ,

```html
<!DOCTYPE html>
<html lang="en">
<head>
<meta charset="utf-8">
<title>Velstride Builders – We're Hiring</title>
<link rel="stylesheet" href="https://fonts.googleapis.com/css2?family=Montserrat:wght@500;600;700;800&family=Jost:wght@400&display=swap">
<style>
  :root {
    --paper: #ffffff;
    --ink: #1a1a1a;
    --brand-black: #0c0c0c;
    --headline-yellow: #f0e01a;
    --accent-yellow: #f0cb1f;
    --rule-yellow: #f2dc1e;
    --blueprint: #eceff1;
  }
  * { margin: 0; padding: 0; box-sizing: border-box; }
  html, body { width: 960px; height: 1200px; overflow: hidden; background: var(--paper); }
  .flyer {
    position: relative;
    width: 960px;
    height: 1200px;
    background: var(--paper);
    overflow: hidden;
    font-family: "Jost", sans-serif;
    color: var(--ink);
  }
  .blueprint {
    position: absolute;
    left: 399px; top: 815px;
    width: 552px; height: 385px;
    background: radial-gradient(ellipse at 45% 40%, var(--blueprint) 0%, rgba(236,239,241,0.5) 45%, rgba(255,255,255,0) 75%);
  }
  .brand-band { position: absolute; left: 0; top: 54px; width: 412px; height: 135px; }
  .brand-name {
    position: absolute;
    left: 0; top: 54px;
    width: 380px; height: 135px;
    display: flex; align-items: center; justify-content: center;
    font-family: "Montserrat", sans-serif;
    font-weight: 500;
    font-size: 27px;
    letter-spacing: 3px;
    color: var(--paper);
  }
  .headline {
    position: absolute;
    right: 73px;
    font-family: "Montserrat", sans-serif;
    font-weight: 700;
    color: var(--headline-yellow);
    line-height: 1;
    text-align: right;
  }
  .headline--were { top: 110px; font-size: 124px; letter-spacing: 4px; right: 76px; }
  .headline--hiring { top: 208px; font-size: 126px; letter-spacing: 26px; right: 48px; }
  .role-title {
    position: absolute;
    left: 310px; top: 352px;
    width: 577px;
    font-family: "Montserrat", sans-serif;
    font-weight: 800;
    font-size: 27px;
    letter-spacing: 2.6px;
    color: var(--headline-yellow);
    white-space: nowrap;
  }
  .rule { position: absolute; left: 68px; width: 813px; height: 3px; background: var(--rule-yellow); }
  .rule--top { top: 403px; }
  .rule--bottom { top: 541px; }
  .intro {
    position: absolute;
    right: 79px; top: 432px;
    text-align: right;
    font-size: 23px;
    line-height: 33px;
    text-transform: uppercase;
    letter-spacing: -0.2px;
  }
  .requirements { list-style: none; position: absolute; left: 68px; top: 610px; width: 820px; }
  .requirement {
    position: relative;
    padding-left: 40px;
    font-size: 16.5px;
    line-height: 24px;
    text-transform: uppercase;
    letter-spacing: -0.1px;
    margin-bottom: 16px;
  }
  .requirement--wrap { text-indent: 19px; padding-left: 40px; }
  .requirement--wrap .cont { display: block; text-indent: 0; margin-left: -19px; }
  .requirement::before {
    content: "";
    position: absolute;
    left: 0; top: 0;
    border-left: 19px solid var(--accent-yellow);
    border-top: 11px solid transparent;
    border-bottom: 11px solid transparent;
  }
  .requirement--gap { margin-top: 6px; }
  .apply { position: absolute; left: 126px; top: 1022px; }
  .apply-label {
    font-family: "Montserrat", sans-serif;
    font-weight: 600;
    font-size: 17px;
    letter-spacing: 2px;
    color: var(--accent-yellow);
  }
  .apply-note { font-family: "Montserrat", sans-serif; font-weight: 500; font-size: 16px; margin-top: 2px; }
  .web-band {
    position: absolute;
    left: 68px; top: 1082px;
    width: 892px; height: 45px;
    background: var(--accent-yellow);
    display: flex; align-items: center;
    padding-left: 58px;
    font-family: "Montserrat", sans-serif;
    font-weight: 500;
    font-size: 21px;
    letter-spacing: 2.4px;
    color: var(--paper);
  }
</style>
</head>
<body>
<main class="flyer">
  <div class="blueprint" role="img" aria-label="Faint architectural elevation drawing of a gabled luxury home"></div>

  <svg class="brand-band" viewBox="0 0 412 135" aria-hidden="true">
    <polygon points="0,0 365,0 412,135 0,135" fill="var(--brand-black)"/>
  </svg>
  <div class="brand-name">VELSTRIDE BUILDERS</div>

  <h1>
    <span class="headline headline--were">WE’RE</span>
    <span class="headline headline--hiring">HIRING</span>
  </h1>
  <h2 class="role-title">CONSTRUCTION PROJECT MANAGER</h2>

  <div class="rule rule--top"></div>
  <p class="intro">We’re looking for a construction project manager<br>who’s passionate about building luxury homes<br>at the highest standards</p>
  <div class="rule rule--bottom"></div>

  <ul class="requirements">
    <li class="requirement requirement--wrap">Experience 5+ years in residential project management with a strong<span class="cont">portfolio of completed homes.</span></li>
    <li class="requirement">Location : Bergen County NJ</li>
    <li class="requirement">Excellent leadership skills, leads teams with confidence and clarity</li>
    <li class="requirement">Communicates seamlessly with architects , engineers, designers and clients</li>
    <li class="requirement">Knows how to manage budgets and timelines without compromising quality</li>
    <li class="requirement">Solves problems with a positive solution first mindset</li>
    <li class="requirement requirement--wrap requirement--gap">Pays attention to every detail because in luxury the small things are<span class="cont">the big things</span></li>
  </ul>

  <div class="apply">
    <p class="apply-label">APPLY NOW</p>
    <p class="apply-note">link in bio or DM to connect.</p>
  </div>

  <div class="web-band">www.velstridebuilders.com</div>
</main>
</body>
</html>
```